Manifesto

I want a manifesto with the following five manifestos for our Not for Profit

- We are a For-purpose organisation
- Every service we offer is free
- Every product we sell funds our services
- Every financial transaction is transparent
- Our service is for the greater good
- Our purpose is always to serve the people
- We are a for purpose organisation

Its to go with this website logo/look/feel www.brightharbour.co.nz

Two attachments:

1. I quite like this look/feel of a manifesto (see attached), I want something clean, professional but I also quite like either Retro modern look feel also like a fresh, and uplifting as its for sick people coming to see us and our funds where anyone buys a product are used for helping those who are sick with healing......so needs something conveyed that is fresh, uplifing yet professional.
2. This attachment is how I wrote this down when inspired of how I wanted Bright Harbour to operate. This is our values chart. It has to say

Also check out our website for our logo, look etc.. it doesnt have to be the same but red somewhere would link back to logo. www.brightharbour.co.nz .

Industry/Entity Type

Financial

```html
<!DOCTYPE html>
<html lang="en">
<head>
<meta charset="utf-8">
<title>Bright Harbour Manifesto</title>
<link rel="stylesheet" href="https://fonts.googleapis.com/css2?family=Arvo:wght@400;700&family=Lobster&family=Lato:wght@400;700;900&display=swap">
<style>
  :root {
    --backdrop: #ececec;
    --poster-red: #8c0019;
    --poster-edge: #5a0010;
    --ink-dark: #43070f;
    --ink-light: #ffffff;
    --shadow: #2e0008;
    --rule: #3d0610;
  }
  * { margin: 0; padding: 0; box-sizing: border-box; }
  html, body {
    width: 1200px; height: 1000px; overflow: hidden;
    background: var(--backdrop);
  }
  .poster {
    position: absolute; left: 275px; top: 53px;
    width: 636px; height: 900px;
    background: radial-gradient(ellipse at 50% 50%, var(--poster-red) 60%, var(--poster-edge) 100%);
    overflow: hidden;
  }
  .line {
    position: absolute; white-space: nowrap; text-align: center;
    line-height: 1;
  }
  .slab { font-family: "Arvo", serif; font-weight: 700; text-transform: uppercase; }
  .slab-lower { font-family: "Arvo", serif; font-weight: 700; }
  .script { font-family: "Lobster", cursive; }
  .sans { font-family: "Lato", sans-serif; font-weight: 700; }
  .dark { color: var(--ink-dark); }
  .light { color: var(--ink-light); text-shadow: 2px 3px 0 var(--shadow); }

  .col-left { left: 22px; width: 314px; }
  .col-right { left: 372px; width: 242px; }
  .full { left: 22px; width: 592px; }
  .values-left { left: 20px; width: 276px; }
  .values-right { left: 336px; width: 278px; }

  .rule { position: absolute; left: 22px; width: 592px; height: 6px; }

  .sign-off { font-family: "Lobster", cursive; color: #111; font-size: 20px; }
  .web { font-family: "Lato", sans-serif; color: var(--ink-light); font-size: 13px; letter-spacing: 3px; }
</style>
</head>
<body>
<main class="poster">
  <!-- Block 1 -->
  <p class="line slab dark col-left" style="top:26px;font-size:56px;">We are a</p>
  <p class="line slab light col-left" style="top:82px;font-size:40px;">For purpose</p>
  <p class="line slab dark col-left" style="top:128px;font-size:35px;">Organisation</p>

  <p class="line script light col-right" style="top:26px;font-size:40px;">Every Service</p>
  <p class="line slab-lower dark col-right" style="top:72px;font-size:22px;letter-spacing:9px;">we offer is</p>
  <p class="line slab dark col-right" style="top:92px;font-size:80px;letter-spacing:4px;">Free</p>

  <svg class="rule" style="top:178px;" viewBox="0 0 592 6" preserveAspectRatio="none" aria-hidden="true"><path d="M0 3 Q148 0 296 3 T592 3 Q296 6 0 3Z" fill="var(--rule)"/></svg>

  <!-- Block 2 -->
  <p class="line slab light full" style="top:200px;font-size:62px;">Every Product</p>
  <p class="line slab-lower dark full" style="top:260px;font-size:38px;">we sell funds our services</p>

  <svg class="rule" style="top:315px;" viewBox="0 0 592 6" preserveAspectRatio="none" aria-hidden="true"><path d="M0 3 Q148 0 296 3 T592 3 Q296 6 0 3Z" fill="var(--rule)"/></svg>

  <!-- Block 3 -->
  <p class="line slab light values-left" style="top:343px;font-size:52px;letter-spacing:12px;">Every</p>
  <p class="line slab light values-left" style="top:400px;font-size:28px;letter-spacing:9px;">Financial</p>
  <p class="line slab dark values-left" style="top:438px;font-size:25px;letter-spacing:6px;">Transaction</p>
  <p class="line slab-lower dark values-left" style="top:467px;font-size:24px;letter-spacing:6px;">is transparent</p>

  <p class="line slab dark values-right" style="top:344px;font-size:25px;letter-spacing:3px;">Our service is</p>
  <p class="line script light values-right" style="top:372px;font-size:43px;">for the greater</p>
  <p class="line sans light values-right" style="top:420px;font-size:80px;">GOOD</p>

  <svg class="rule" style="top:516px;" viewBox="0 0 592 6" preserveAspectRatio="none" aria-hidden="true"><path d="M0 3 Q148 0 296 3 T592 3 Q296 6 0 3Z" fill="var(--rule)"/></svg>

  <!-- Block 4 -->
  <p class="line slab dark full" style="top:545px;font-size:52px;letter-spacing:4px;">Our purpose is</p>
  <p class="line script light full" style="top:594px;font-size:52px;">always to serve the people</p>

  <svg class="rule" style="top:676px;" viewBox="0 0 592 6" preserveAspectRatio="none" aria-hidden="true"><path d="M0 3 Q148 0 296 3 T592 3 Q296 6 0 3Z" fill="var(--rule)"/></svg>

  <!-- Block 5 -->
  <p class="line slab dark full" style="top:700px;font-size:41px;letter-spacing:1px;">We are a for purpose</p>
  <p class="line script light full" style="top:740px;font-size:104px;">organisation</p>

  <p class="line sign-off full" style="top:842px;">Bright Harbour Manifesto</p>
  <p class="line web full" style="top:869px;">www.brightharbour.co.nz</p>
</main>
</body>
</html>
```